Software allocation system needs a business card design

We need a business card designed for our software platform - www.tallivo.com.au

At the moment the logo and website is all black and white, we are happy for suggestions on implementing some colour throughout either the logo or business card.

Industry/Entity Type

Software

Font styles to use
Sans Serif

Colors

Designer to choose colors to be used in the design.

```html
<!DOCTYPE html>
<html lang="en">
<head>
<meta charset="utf-8">
<title>Tallivo Business Card</title>
<link rel="stylesheet" href="https://fonts.googleapis.com/css2?family=Josefin+Sans:wght@300;400&display=swap">
<style>
  :root {
    --page: #e9ecee;
    --card: #ffffff;
    --ink: #3e4a54;
    --teal: #8ccfd3;
    --teal-soft: #a6d3d9;
    --blue: #2a88bd;
    --blue-deep: #1d74a6;
    --navy: #1f5f86;
    --white: #ffffff;
  }
  * { margin: 0; padding: 0; box-sizing: border-box; }
  html, body {
    width: 1200px;
    height: 900px;
    overflow: hidden;
    background: var(--page);
    font-family: "Josefin Sans", sans-serif;
  }
  .card {
    position: absolute;
    left: 150px;
    top: 175px;
    width: 900px;
    height: 549px;
    background: var(--card);
    overflow: hidden;
    box-shadow: 0 14px 36px rgba(30, 50, 70, 0.18);
  }
  .card-shapes {
    position: absolute;
    inset: 0;
  }
  .brand {
    position: absolute;
    left: 78px;
    top: 118px;
  }
  .brand-name {
    display: flex;
    align-items: center;
    gap: 18px;
    font-weight: 300;
    font-size: 74px;
    letter-spacing: 6px;
    color: var(--ink);
    line-height: 1;
  }
  .brand-dot {
    width: 46px;
    height: 46px;
    border-radius: 50%;
    background: var(--teal);
  }
  .brand-tagline {
    margin-top: 16px;
    margin-left: 4px;
    font-size: 21px;
    font-weight: 400;
    letter-spacing: 2px;
    text-transform: uppercase;
    color: var(--teal);
  }
  .contact {
    position: absolute;
    left: 352px;
    top: 362px;
    color: var(--white);
  }
  .contact-title {
    font-size: 34px;
    font-weight: 400;
    color: var(--navy);
    margin-bottom: 12px;
  }
  .contact-line {
    font-size: 24px;
    font-weight: 300;
    line-height: 1.3;
  }
</style>
</head>
<body>
  <div class="card">
    <svg class="card-shapes" width="900" height="549" viewBox="0 0 900 549">
      <defs>
        <linearGradient id="band-tone" x1="0" y1="1" x2="1" y2="0">
          <stop offset="0" stop-color="var(--blue-deep)"/>
          <stop offset="1" stop-color="var(--blue)"/>
        </linearGradient>
      </defs>
      <polygon class="contact-panel" points="200,549 330,355 900,210 900,549" fill="var(--teal-soft)"/>
      <g role="img" aria-label="Diagonal band with a faceted blue triangle pattern">
        <polygon class="pattern-band" points="0,385 900,150 900,210 330,355 200,549 0,549" fill="url(#band-tone)"/>
      </g>
    </svg>

    <div class="brand">
      <div class="brand-name"><span class="brand-dot"></span>TALLIVO</div>
      <div class="brand-tagline">Planning &amp; Compliance for Heavy Industry</div>
    </div>

    <div class="contact">
      <h2 class="contact-title">Contac Us</h2>
      <p class="contact-line">PO Box 218</p>
      <p class="contact-line">Kirrawee NSW 2232</p>
      <p class="contact-line">hello@tallivo.com.au</p>
    </div>
  </div>
</body>
</html>
```